BOLD & MINIMALIST DESIGN NEEDED

We want a very bold but minimalistic business card design that is impactful and utilizes both sides of the business card. Our current logo is included for your use.

We want bold fonts and good use of negative space. We don't want the logo to overpower the design.

Target Market(s)

Professionals who are building new commercial buildings.

Industry/Entity Type

Construction

Contact Information for Business Card

Name, Title, email, office phone, cell phone, website

Font styles to use
Serif
Sans Serif

Requirements
Must have
• Bold design!

```html
<!DOCTYPE html>
<html lang="en">
<head>
<meta charset="utf-8">
<title>Ridgeline Design + Build – Business Card</title>
<link href="https://fonts.googleapis.com/css2?family=Arimo:wght@400;700&display=swap" rel="stylesheet">
<style>
  :root {
    --bg: #b9b9b9;
    --white: #ffffff;
    --green-light: #7fc62a;
    --green: #5f9a1c;
    --green-mid: #4f7f18;
    --green-dark: #355a0e;
    --ink: #1d1d1d;
    --grey-text: #555555;
  }
  * { margin: 0; padding: 0; box-sizing: border-box; }
  html, body {
    width: 1200px; height: 802px; overflow: hidden;
    background: var(--bg);
    font-family: "Arimo", Arial, sans-serif;
  }
  .stage {
    width: 1200px; height: 802px;
    display: flex; align-items: center; justify-content: center; gap: 40px;
  }
  .card {
    position: relative;
    width: 540px; height: 309px;
    border-radius: 18px;
    overflow: hidden;
  }

  /* Brand name placeholder: one colour, one weight, one plain square */
  .brand {
    display: flex; align-items: center; gap: 10px;
    font-family: "Arimo", Arial, sans-serif;
    font-weight: 700;
    line-height: 1;
    white-space: nowrap;
  }
  .brand__square { width: 18px; height: 18px; flex: none; background: currentColor; }

  /* Front side */
  .card--front {
    background: linear-gradient(150deg, var(--white) 0%, var(--white) 38%, #cfe6b0 55%, var(--green-light) 72%, var(--green) 100%);
  }
  .card--front .brand {
    position: absolute; left: 36px; top: 196px;
    font-size: 22px;
    color: var(--green-dark);
  }
  .contact {
    position: absolute; left: 290px; top: 34px;
  }
  .contact__name {
    font-weight: 700; font-size: 26px; color: var(--green-light);
  }
  .contact__title {
    font-size: 13px; color: var(--grey-text); margin-top: 4px; margin-bottom: 14px;
  }
  .contact__list { list-style: none; }
  .contact__item {
    display: flex; align-items: center; gap: 10px;
    font-size: 13px; color: var(--ink); margin-bottom: 7px;
  }
  .contact__icon { width: 14px; height: 14px; flex: none; }
  .address {
    position: absolute; left: 0; right: 0; bottom: 22px;
    text-align: center; font-size: 14px; color: var(--white); letter-spacing: 0.3px;
  }

  /* Back side */
  .card--back {
    background: radial-gradient(ellipse at 50% 45%, var(--green) 0%, var(--green-mid) 55%, var(--green-dark) 100%);
    display: flex; align-items: center; justify-content: center;
  }
  .card--back .brand {
    font-size: 30px;
    color: var(--white);
  }
  .card--back .brand__square { width: 24px; height: 24px; }
</style>
</head>
<body>
<main class="stage">
  <section class="card card--front" aria-label="Business card front">
    <div class="brand">
      <span class="brand__square" aria-hidden="true"></span>
      <span class="brand__name">Ridgeline Design + Build</span>
    </div>

    <div class="contact">
      <p class="contact__name">Marcus Bell</p>
      <p class="contact__title">Founder &amp; CEO</p>
      <ul class="contact__list">
        <li class="contact__item">
          <svg class="contact__icon" viewBox="0 0 24 24" aria-hidden="true"><path fill="#5f9a1c" d="M6.6 10.8a15.1 15.1 0 0 0 6.6 6.6l2.2-2.2c.3-.3.7-.4 1-.2 1.1.4 2.3.6 3.6.6.6 0 1 .4 1 1V20c0 .6-.4 1-1 1A17 17 0 0 1 3 4c0-.6.4-1 1-1h3.5c.6 0 1 .4 1 1 0 1.3.2 2.5.6 3.6.1.3 0 .7-.2 1z"/></svg>
          021-436-587-190
        </li>
        <li class="contact__item">
          <svg class="contact__icon" viewBox="0 0 24 24" aria-hidden="true"><rect x="6" y="2" width="12" height="20" rx="2" fill="#5f9a1c"/><rect x="8" y="5" width="8" height="12" fill="#ffffff"/></svg>
          055-234-567-890
        </li>
        <li class="contact__item">
          <svg class="contact__icon" viewBox="0 0 24 24" aria-hidden="true"><path fill="#5f9a1c" d="M2 21 23 12 2 3v7l15 2-15 2z"/></svg>
          info@ridgebuild.com
        </li>
        <li class="contact__item">
          <svg class="contact__icon" viewBox="0 0 24 24" aria-hidden="true"><circle cx="12" cy="12" r="10" fill="#5f9a1c"/><path d="M2 12h20M12 2c3 3 3 17 0 20M12 2c-3 3-3 17 0 20" stroke="#ffffff" stroke-width="1.5" fill="none"/></svg>
          www.ridgebuild.com
        </li>
      </ul>
    </div>

    <p class="address">4720 Harbor Pine Pkwy 210-B, FL 32400</p>
  </section>

  <section class="card card--back" aria-label="Business card back">
    <div class="brand">
      <span class="brand__square" aria-hidden="true"></span>
      <span class="brand__name">Ridgeline Design + Build</span>
    </div>
  </section>
</main>
</body>
</html>
```